Brightfield Ventures Inc. Letterhead

Creation of attractive and eye catching letterhead for a business start-up for the construction industry. Letterhead must relate to construction, but avoid standard hammer and tools in the design.

I forgot to add some details, sorry about that. Some pertinent info: Ph: 916-555-0187 brightfieldventures.example 448 Willowmere Ave, Ste 210 Folsom, CA 95999 info@brightfieldventures.example not sure if slogan should be in there" “Connecting construction professionals to create a purpose driven industry.” must be able to be used in word. Thanks!

```html
<!DOCTYPE html>
<html lang="en">
<head>
<meta charset="utf-8">
<title>Brightfield Ventures Inc. Letterhead</title>
<link rel="stylesheet" href="https://fonts.googleapis.com/css2?family=Open+Sans:wght@400;600;700&display=swap">
<style>
  :root {
    --brand-red: #c0121b;
    --brand-navy: #131b4d;
    --ink: #2b2b2b;
    --muted: #555;
    --paper: #ffffff;
    --backdrop: #ececec;
  }
  * { box-sizing: border-box; margin: 0; padding: 0; }
  html, body { width: 1200px; height: 784px; overflow: hidden; }
  body {
    background: var(--backdrop);
    font-family: "Open Sans", Arial, sans-serif;
    color: var(--ink);
    display: flex; align-items: center; justify-content: center;
  }
  .letterhead {
    position: relative;
    width: 530px; height: 750px;
    background: var(--paper);
    box-shadow: 0 2px 12px rgba(0,0,0,.12);
    overflow: hidden;
  }
  .edge-red { position: absolute; left: 0; top: 0; width: 30px; height: 230px; background: var(--brand-red); }
  .edge-navy { position: absolute; left: 0; top: 240px; width: 22px; bottom: 0; background: var(--brand-navy); }
  .edge-line { position: absolute; left: 26px; top: 240px; width: 4px; bottom: 0; background: var(--brand-red); }

  .brand { position: absolute; left: 62px; top: 70px; display: flex; align-items: center; gap: 8px; }
  .brand-mark { width: 12px; height: 12px; background: var(--brand-red); }
  .brand-name { font-weight: 700; font-size: 17px; color: var(--brand-navy); letter-spacing: .3px; }

  .letter-body { position: absolute; left: 62px; right: 58px; top: 160px; font-size: 10.5px; line-height: 1.55; color: var(--ink); }
  .salutation { font-weight: 700; font-size: 13px; margin-bottom: 12px; }
  .letter-body p { margin-bottom: 14px; }

  .signature { position: absolute; left: 110px; top: 470px; width: 120px; height: 60px; background: linear-gradient(135deg, #e9e9ee, #d9d9e0); border-radius: 4px; }

  .footer { position: absolute; left: 62px; bottom: 30px; display: flex; align-items: center; gap: 14px; font-size: 9px; color: var(--muted); }
  .contact-list { list-style: none; line-height: 1.6; }
  .contact-list li { display: flex; align-items: center; gap: 5px; }
  .contact-list svg { width: 8px; height: 8px; fill: var(--brand-red); }
  .footer-divider { width: 1px; height: 30px; background: #cfcfcf; }
  .company-line { color: var(--brand-red); font-weight: 700; font-size: 10px; }
  .address-line { line-height: 1.5; }

  .web-tab { position: absolute; right: 0; bottom: 140px; width: 26px; height: 150px; background: var(--brand-red); border-radius: 4px 0 0 4px; }
  .web-tab span { position: absolute; left: 50%; top: 50%; transform: translate(-50%,-50%) rotate(-90deg); white-space: nowrap; color: #fff; font-size: 8.5px; }
</style>
</head>
<body>
  <article class="letterhead">
    <div class="edge-red"></div>
    <div class="edge-navy"></div>
    <div class="edge-line"></div>

    <header class="brand">
      <span class="brand-mark"></span>
      <span class="brand-name">Brightfield Ventures Inc.</span>
    </header>

    <section class="letter-body">
      <p class="salutation">Dear Mr. Ellis,</p>
      <p>Lorem Ipsum is simply dummy text of the printing and typesetting industry. Lorem Ipsum has been the industry's standard dummy text ever since the 1500s, when an unknown printer took a galley of type and scrambled it to make a type specimen book. It has survived not only five centuries, but also the leap into electronic typesetting, remaining essentially unchanged.</p>
      <p>The standard chunk of Lorem Ipsum used since the 1500s is reproduced below for those interested. Sections 1.10.32 and 1.10.33 from "de Finibus Bonorum et Malorum" by M. Tullan are also reproduced in their exact original form, accompanied by English versions from the 1914 translation by R. Holloway.</p>
      <p>Lorem Ipsum is simply dummy text of the printing and typesetting industry. Lorem Ipsum has been the industry's standard dummy text ever since the 1500s, when an unknown printer took a galley of type and scrambled it to make a type specimen book. It has survived not only five centuries, but also the leap into electronic typesetting, remaining essentially unchanged. It was popularised in the</p>
    </section>

    <div class="signature" role="img" aria-label="Handwritten signature"></div>

    <footer class="footer">
      <ul class="contact-list">
        <li><svg viewBox="0 0 10 10"><path d="M2 0h2l1 3-1.5 1a6 6 0 0 0 2.5 2.5L7 5l3 1v2a2 2 0 0 1-2 2A8 8 0 0 1 0 2a2 2 0 0 1 2-2z"/></svg>916-555-0187</li>
        <li><svg viewBox="0 0 10 10"><path d="M0 2h10v6H0z M0 2l5 3.5L10 2" stroke="#fff" stroke-width=".8"/></svg>info@brightfieldventures.example</li>
      </ul>
      <span class="footer-divider"></span>
      <div>
        <div class="company-line">Brightfield Ventures Inc.</div>
        <div class="address-line">448 Willowmere Ave, Ste 210, Folsom, CA 95999</div>
      </div>
    </footer>

    <div class="web-tab"><span>www.brightfieldventures.example</span></div>
  </article>
</body>
</html>
```